Harbourline Electrical Solutions

On one side. LOGO (underneath:) Commercial Industrial Residential

- NAME & CONTACT DETAILS

Marcus T. Hollings
Project Manager

(Cell icon) (441) 555-0187
(Email icon) hlelectricalsolutions@mailvento.com
(Facebook & Instagram icons )@hlelectricalsolutions

Other side: LOGO - underneath ELECTRICAL CONSTRUCTION & MAINTENANCE . LED LIGHTING & AUTOMATION . LIFE SAFETY SYSTEMS (FIRE ALARM / SECURITY) . DATA & COMMUNICATION

```html
<!DOCTYPE html>
<html lang="en">
<head>
<meta charset="utf-8">
<title>Harbourline Electrical Solutions – Business Card</title>
<link rel="stylesheet" href="https://fonts.googleapis.com/css2?family=Montserrat:wght@500;600&family=Roboto:wght@400&family=Exo+2:ital,wght@1,600&display=swap">
<style>
  :root{
    --bg:#2e2f31;
    --teal:#0d5675;
    --band:#424749;
    --white:#ffffff;
    --ink:#2b2f33;
  }
  *{box-sizing:border-box;margin:0;padding:0}
  html,body{width:799px;height:1200px;overflow:hidden;background:var(--bg)}
  .canvas{position:relative;width:799px;height:1200px}
  .card{position:absolute;left:90px;width:620px;height:354px;overflow:hidden;box-shadow:0 10px 30px rgba(0,0,0,.45)}
  .card--front{top:150px;background:var(--teal)}
  .card--back{top:700px;background:var(--teal)}

  /* front */
  .front__band{position:absolute;left:0;right:0;top:140px;height:124px;background:var(--band)}
  .front__mark{position:absolute;left:0;right:0;top:42px;display:flex;align-items:center;justify-content:center;gap:16px}
  .front__square{width:22px;height:22px;background:var(--white)}
  .front__name{font-family:"Montserrat",sans-serif;font-weight:600;color:var(--white);font-size:24px;letter-spacing:4px;line-height:1.15;text-transform:uppercase}
  .front__services{position:absolute;left:0;right:0;top:170px;text-align:center;font-family:"Roboto",sans-serif;color:var(--white);font-size:15px;line-height:1.6}
  .front__social{position:absolute;left:0;right:0;top:286px;display:flex;justify-content:center;align-items:center;gap:10px;font-family:"Roboto",sans-serif;color:var(--white);font-size:16px}
  .dot{width:14px;height:14px;border-radius:50%;border:2px solid var(--white);flex:none}

  /* back */
  .back__shape{position:absolute;inset:0}
  .back__mark{position:absolute;left:34px;top:92px;width:230px}
  .back__name{font-family:"Montserrat",sans-serif;font-weight:600;color:var(--teal);font-size:21px;letter-spacing:3px;line-height:1.2;text-transform:uppercase}
  .back__sectors{margin-top:12px;font-family:"Montserrat",sans-serif;font-weight:500;color:var(--ink);font-size:8.5px;letter-spacing:1.2px}
  .back__contact{position:absolute;left:330px;top:108px;color:var(--white)}
  .person__name{font-family:"Exo 2",sans-serif;font-style:italic;font-weight:600;font-size:22px}
  .person__role{font-family:"Roboto",sans-serif;font-size:14px;margin-top:2px}
  .contact__list{list-style:none;margin-top:26px;font-family:"Roboto",sans-serif;font-size:14px;line-height:1.65}
  .contact__list li{display:flex;align-items:center;gap:8px}
  .contact__list svg{width:13px;height:13px;flex:none}
</style>
</head>
<body>
<main class="canvas">

  <section class="card card--front" aria-label="Card front">
    <div class="front__band"></div>
    <div class="front__mark">
      <span class="front__square"></span>
      <div class="front__name">Harbourline<br>Electrical<br>Solutions</div>
    </div>
    <p class="front__services">
      Electrical Construction &amp; Maintenance &nbsp;|&nbsp; Led Lighting &amp; Automation<br>
      Life Safety Systems (Fire Alarm/Security) &nbsp;|&nbsp; Data &amp; Communication
    </p>
    <div class="front__social"><span class="dot"></span>@hlelectricalsolutions</div>
  </section>

  <section class="card card--back" aria-label="Card back">
    <svg class="back__shape" viewBox="0 0 620 354" preserveAspectRatio="none">
      <path d="M0 0 H312 C270 110 240 250 206 354 H0 Z" fill="#424749"/>
      <path d="M0 0 H298 C256 110 226 250 192 354 H0 Z" fill="#ffffff"/>
    </svg>
    <div class="back__mark">
      <div class="back__name">Harbourline<br>Electrical<br>Solutions</div>
      <p class="back__sectors">COMMERCIAL | INDUSTRIAL | RESIDENTIAL</p>
    </div>
    <div class="back__contact">
      <h1 class="person__name">Marcus T. Hollings</h1>
      <p class="person__role">Project Manager</p>
      <ul class="contact__list">
        <li><svg viewBox="0 0 16 16"><path d="M4 1h3l1 4-2 1c1 2 2 3 4 4l1-2 4 1v3c0 1-1 2-2 2C7 14 2 9 2 3c0-1 1-2 2-2z" fill="#fff"/></svg>(441) 555-0187</li>
        <li><svg viewBox="0 0 16 16"><rect x="1" y="3" width="14" height="10" fill="#fff"/><path d="M1 3l7 6 7-6" fill="none" stroke="#0d5675" stroke-width="1.5"/></svg>hlelectricalsolutions@mailvento.com</li>
        <li><svg viewBox="0 0 16 16"><circle cx="8" cy="8" r="6" fill="none" stroke="#fff" stroke-width="2"/></svg>@hlelectricalsolutions</li>
      </ul>
    </div>
  </section>

</main>
</body>
</html>
```